Executive recruiting firm in need of business card design

Executive recruiting firm looking for a sleek, classy and modern business card design; card itself will be square shape, rounded edges and soft touch paper, our colors are dark blues in the navy color scale, silvers and grays. Reference our website for a better idea of our company's feel and goals at Tarvex-Up.com - our company message is "Employee Engagement Begins at Recruitment" this should be on the card

```html
<!DOCTYPE html>
<html lang="en">
<head>
<meta charset="UTF-8">
<title>Tarvex-Up Business Card</title>
<link rel="stylesheet" href="https://fonts.googleapis.com/css2?family=Source+Sans+3:wght@300;400;600;700&display=swap">
<style>
  :root {
    --backdrop: #000000;
    --card-light: #f3f3f3;
    --navy: #161a48;
    --ink: #1b1d3f;
    --silver: #8a8c9e;
    --white: #ffffff;
    --mist: #c9cbe0;
  }
  * { margin: 0; padding: 0; box-sizing: border-box; }
  html, body {
    width: 1200px;
    height: 900px;
    overflow: hidden;
    background: var(--backdrop);
    font-family: "Source Sans 3", "Myriad Pro", Arial, sans-serif;
  }
  .canvas { position: relative; width: 1200px; height: 900px; }

  .card { position: absolute; top: 200px; width: 310px; height: 502px; overflow: hidden; }
  .card--front {
    left: 265px;
    background: var(--card-light);
    border-radius: 62px 0 62px 0;
  }
  .card--back {
    left: 641px;
    width: 308px;
    background: var(--navy);
    border-radius: 0 62px 0 62px;
  }

  .brand { position: absolute; text-align: right; }
  .brand__name {
    display: block;
    font-size: 34px;
    font-weight: 300;
    letter-spacing: 4px;
    line-height: 38px;
    white-space: nowrap;
  }
  .brand__tagline {
    display: block;
    margin-top: 4px;
    font-size: 8.5px;
    font-weight: 400;
    letter-spacing: 0.6px;
    white-space: nowrap;
  }

  .card--front .brand { right: 32px; top: 70px; }
  .card--front .brand__name { color: var(--navy); }
  .card--front .brand__tagline { color: var(--silver); }

  .card--back .brand { right: 36px; top: 366px; }
  .card--back .brand__name { color: var(--white); }
  .card--back .brand__tagline { color: var(--mist); }

  .person { position: absolute; left: 35px; top: 305px; color: var(--ink); }
  .person__name { font-size: 19px; font-weight: 700; line-height: 22px; }
  .person__role { font-size: 14px; font-weight: 400; line-height: 18px; }

  .address {
    position: absolute; left: 35px; top: 367px;
    font-size: 14px; line-height: 15.5px; color: var(--ink); font-style: normal;
  }

  .contacts { position: absolute; left: 35px; top: 414px; list-style: none; color: var(--ink); }
  .contacts__item {
    display: flex; align-items: center; gap: 7px;
    font-size: 14px; line-height: 21px;
  }
  .contacts__icon { width: 11px; height: 11px; fill: var(--ink); flex: none; }
</style>
</head>
<body>
<main class="canvas">

  <section class="card card--front" aria-label="Card front">
    <div class="brand">
      <span class="brand__name">TARVEX UP</span>
      <span class="brand__tagline">Employee Engagement Begins at Recruitment</span>
    </div>

    <div class="person">
      <p class="person__name">Daniel Whitford</p>
      <p class="person__role">Managing Director</p>
    </div>

    <address class="address">
      12345, Address Goes Here<br>
      Country Name, 123456
    </address>

    <ul class="contacts">
      <li class="contacts__item">
        <svg class="contacts__icon" viewBox="0 0 24 24" aria-hidden="true"><path d="M6.6 10.8a15.1 15.1 0 0 0 6.6 6.6l2.2-2.2a1 1 0 0 1 1-.25 11.4 11.4 0 0 0 3.6.6 1 1 0 0 1 1 1V20a1 1 0 0 1-1 1A17 17 0 0 1 3 4a1 1 0 0 1 1-1h3.5a1 1 0 0 1 1 1c0 1.25.2 2.45.6 3.6a1 1 0 0 1-.25 1z"/></svg>
        (044)-318-2705
      </li>
      <li class="contacts__item">
        <svg class="contacts__icon" viewBox="0 0 24 24" aria-hidden="true"><path d="M2 5h20v2l-10 7L2 7z M2 8.5l10 7 10-7V19H2z"/></svg>
        info@tarvex-up.com
      </li>
      <li class="contacts__item">
        <svg class="contacts__icon" viewBox="0 0 24 24" aria-hidden="true"><circle cx="12" cy="12" r="10"/><path d="M7 8c2 0 3 1 3 3s2 2 2 4-1 3-1 4M15 5c0 2 1 3 3 3" fill="none" stroke="#f3f3f3" stroke-width="1.6"/></svg>
        www.Tarvex-Up.com
      </li>
    </ul>
  </section>

  <section class="card card--back" aria-label="Card back">
    <div class="brand">
      <span class="brand__name">TARVEX UP</span>
      <span class="brand__tagline">Employee Engagement Begins at Recruitment</span>
    </div>
  </section>

</main>
</body>
</html>
```